Coffeeshop menu for filter tip

We want to have a cannabis (coffeeshop) menu in the size 25mm wide x 60mm wide. Some examples attached.

it must have the following text:
Menu

WEED p/g
Oblivane €16
Cloudplum €14
Tide Runner €14
Quincefig €16
Mega Marsh €14
Grey Heron €14

HASH p/g
Tashar Amber €12
Pebble Frost€11
Lime Dunes €14
Ash Petal €10

Target Market(s)

tourist in Amsterdam

Requirements
Nice to have
• cannabis sign leaf
• No Cigarettes allowed symbol

```html
<!DOCTYPE html>
<html lang="en">
<head>
<meta charset="utf-8">
<title>Coffeeshop Menu</title>
<link rel="stylesheet" href="https://fonts.googleapis.com/css2?family=Oswald:wght@500&family=Roboto+Condensed:wght@300;700&family=Kaushan+Script&display=swap">
<style>
  :root {
    --page-bg: #e3e3e3;
    --card-top: #1e2420;
    --card-bottom: #111813;
    --gold-light: #ffd84a;
    --gold: #f2b21c;
    --gold-dark: #c98a10;
    --text: #ffffff;
    --sign-red: #d32b2b;
  }
  * { margin: 0; padding: 0; box-sizing: border-box; }
  html, body { width: 1200px; height: 2457px; overflow: hidden; background: var(--page-bg); }
  .menu-card {
    position: absolute; left: 138px; top: 125px; width: 922px; height: 2205px;
    background: var(--card-bottom); overflow: hidden;
    box-shadow: 10px 12px 18px rgba(0,0,0,.35);
  }
  .card-head {
    position: absolute; left: 0; top: 0; width: 100%; height: 733px;
    background: var(--card-top);
  }
  .leaf-emblem {
    position: absolute; left: 218px; top: 70px; width: 501px; height: 467px;
    background: radial-gradient(ellipse at 50% 45%, var(--gold-light), var(--gold) 45%, rgba(201,138,16,0) 72%);
  }
  .menu-title {
    position: absolute; left: 96px; top: 545px; width: 740px;
    display: flex; justify-content: space-between;
    font-family: "Oswald", sans-serif; font-weight: 500; font-size: 158px; line-height: 1;
    background: linear-gradient(180deg, var(--gold-light), var(--gold-dark));
    -webkit-background-clip: text; background-clip: text; color: transparent;
  }
  .no-smoking-corner { position: absolute; right: 0; top: 0; width: 372px; height: 368px; }
  .section-head {
    position: absolute; left: 70px; width: 790px;
    display: flex; justify-content: space-between; align-items: center;
  }
  .section-name {
    font-family: "Kaushan Script", cursive; font-size: 128px; line-height: 1;
    background: linear-gradient(180deg, var(--gold-light), var(--gold-dark));
    -webkit-background-clip: text; background-clip: text; color: transparent;
  }
  .unit {
    font-family: "Roboto Condensed", sans-serif; font-weight: 300; font-size: 80px;
    color: var(--text); margin-right: 8px;
  }
  .price-list { position: absolute; left: 70px; width: 790px; list-style: none; }
  .price-list li {
    height: 104px; display: flex; justify-content: space-between; align-items: center;
    font-family: "Roboto Condensed", sans-serif; color: var(--text); font-size: 88px;
  }
  .item-name { font-weight: 300; }
  .item-price { font-weight: 700; }
</style>
</head>
<body>
  <main class="menu-card">
    <header class="card-head">
      <div class="leaf-emblem" role="img" aria-label="Golden cannabis leaf emblem"></div>
      <h1 class="menu-title"><span>M</span><span>E</span><span>N</span><span>U</span></h1>
    </header>

    <svg class="no-smoking-corner" viewBox="0 0 372 368" aria-label="No cigarettes">
      <defs>
        <linearGradient id="goldBand" x1="0" y1="0" x2="1" y2="1">
          <stop offset="0" stop-color="#ffd84a"/>
          <stop offset="1" stop-color="#c98a10"/>
        </linearGradient>
      </defs>
      <polygon points="0,0 372,0 372,368" fill="url(#goldBand)"/>
      <g transform="translate(186 184) rotate(45)">
        <text x="-40" y="-12" text-anchor="middle" font-family="Oswald, sans-serif" font-weight="500" font-size="40" fill="#111813">NO CIGARETTES</text>
      </g>
      <g transform="translate(277 95)">
        <circle r="46" fill="#111813"/>
        <circle r="38" fill="#ffffff"/>
        <rect x="-26" y="-6" width="40" height="12" fill="#ffffff" stroke="#111813" stroke-width="3"/>
        <rect x="14" y="-6" width="12" height="12" fill="#e08a2a" stroke="#111813" stroke-width="3"/>
        <circle r="34" fill="none" stroke="var(--sign-red)" stroke-width="8"/>
        <line x1="-24" y1="-24" x2="24" y2="24" stroke="var(--sign-red)" stroke-width="8"/>
      </g>
    </svg>

    <section class="weed">
      <div class="section-head" style="top:812px"><h2 class="section-name">Weed</h2><span class="unit">p/g</span></div>
      <ul class="price-list" style="top:934px">
        <li><span class="item-name">Oblivane</span><span class="item-price">€16</span></li>
        <li><span class="item-name">Cloudplum</span><span class="item-price">€14</span></li>
        <li><span class="item-name">Tide Runner</span><span class="item-price">€14</span></li>
        <li><span class="item-name">Quincefig</span><span class="item-price">€16</span></li>
        <li><span class="item-name">Mega Marsh</span><span class="item-price">€14</span></li>
        <li><span class="item-name">Grey Heron</span><span class="item-price">€14</span></li>
      </ul>
    </section>

    <section class="hash">
      <div class="section-head" style="top:1604px"><h2 class="section-name">Hash</h2><span class="unit">p/g</span></div>
      <ul class="price-list" style="top:1755px">
        <li><span class="item-name">Tashar Amber</span><span class="item-price">€12</span></li>
        <li><span class="item-name">Pebble Frost</span><span class="item-price">€11</span></li>
        <li><span class="item-name">Lime Dunes</span><span class="item-price">€14</span></li>
        <li><span class="item-name">Ash Petal</span><span class="item-price">€10</span></li>
      </ul>
    </section>
  </main>
</body>
</html>
```